Business card for Eyelash extension salon in Beverly Hills,California USA

We need new business card for our salon in Beverly Hills. The salon name is 'Lashvera' . We would like to have...Business name: Lashvera Name of person: will provide later Address 4720 N.Alder Crest Ave Beverly Hills , CA 90210 Phone: will provide later (Text only) Web: www.lashverastudio.example Snapgrid icon, Circlebook icon follow us for seasonal campaign and news @lashverastudiolounge Design should look elegant, high-end, clean, simple, cohesive with my brand. Please refer my brand board. Business name color will be metallic bronzy color. Im thinking grey background or white background. Thanks

Target Market(s)

25-35. Gender neutral. People who are in Entertainment business industry.
This is High-end Eyelash extension salon in Beverly Hills

Industry/Entity Type

Beauty Salon

Contact Information for Business Card

Business name: Lashvera
Name of person: will provide later
Address 4720 N.Alder Crest Ave Beverly Hills , CA 90210
Phone: will provide later (Text only)
Web: www.lashverastudio.example
Snapgrid icon, Circlebook icon
follow us for seasonal campaign and news @lashverastudiolounge

Requirements
Must have
• Beautiful, elegant, clean and simple look but very attractive and modern
Should not have
• We don't like too clutter, too busy designs.

```html
<!DOCTYPE html>
<html lang="en">
<head>
<meta charset="utf-8">
<title>Lashvera Business Card</title>
<link rel="stylesheet" href="https://fonts.googleapis.com/css2?family=Open+Sans:wght@300;400;600;700&display=swap">
<style>
  :root {
    --page: #e4e4e4;
    --card: #2c2b2c;
    --card-shade: #323132;
    --bronze: #a6764f;
    --ink: #ecebe8;
    --muted: #9c9895;
    --rule: #5c5958;
  }
  * { box-sizing: border-box; margin: 0; padding: 0; }
  html, body {
    width: 1200px; height: 782px; overflow: hidden;
    background: var(--page);
    font-family: "Open Sans", Arial, sans-serif;
  }
  .canvas { position: relative; width: 1200px; height: 782px; }
  .card {
    position: absolute; left: 300px; width: 600px; height: 343px;
    background: var(--card); overflow: hidden;
    box-shadow: 0 6px 18px rgba(0,0,0,.18);
  }
  .card--back { top: 38px; }
  .card--front { top: 401px; }

  .pattern-field {
    position: absolute; inset: 0;
    background: linear-gradient(135deg, var(--card) 0%, var(--card-shade) 50%, var(--card) 100%);
  }
  .back-name {
    position: absolute; left: 0; right: 0; top: 196px; text-align: center;
    padding-left: 40px;
    font-size: 26px; font-weight: 300; color: #fff; letter-spacing: .5px;
  }

  .brand {
    position: absolute; right: 70px; top: 92px; text-align: right;
  }
  .brand__name {
    font-size: 48px; font-weight: 300; color: var(--bronze); line-height: 1;
  }
  .brand__place {
    margin-top: 8px; font-size: 8px; letter-spacing: 2.5px;
    color: var(--bronze);
  }

  .contact { position: absolute; left: 34px; top: 150px; }
  .contact__name {
    font-size: 16px; font-weight: 700; color: var(--bronze); letter-spacing: .6px;
  }
  .contact__line {
    display: flex; align-items: center; gap: 7px;
    margin-top: 5px; font-size: 13px; color: var(--ink);
  }
  .contact__line svg { width: 11px; height: 11px; flex: none; }

  .rule {
    position: absolute; left: 34px; right: 34px; height: 1px; background: var(--rule);
  }
  .rule--upper { top: 222px; }
  .rule--lower { top: 282px; }

  .address {
    position: absolute; right: 36px; top: 232px; text-align: right;
    font-size: 14px; line-height: 20px; color: var(--ink);
  }

  .follow {
    position: absolute; left: 34px; top: 296px;
    display: flex; align-items: center; gap: 6px;
    font-size: 13.5px; color: var(--ink);
  }
  .social-dot {
    width: 14px; height: 14px; border-radius: 50%; background: var(--muted); flex: none;
  }
  .follow__text { margin-left: 4px; }
  .follow__handle { font-weight: 700; }
</style>
</head>
<body>
<main class="canvas">

  <section class="card card--back" aria-label="Card back">
    <div class="pattern-field" role="img" aria-label="Faint repeated brand-name pattern across the card"></div>
    <p class="back-name">Lashvera</p>
  </section>

  <section class="card card--front" aria-label="Card front">
    <div class="brand">
      <p class="brand__name">Lashvera</p>
      <p class="brand__place">BEVERLY HILLS</p>
    </div>

    <div class="contact">
      <p class="contact__name">DANIEL MARLOW</p>
      <p class="contact__line">
        <svg viewBox="0 0 12 12" aria-hidden="true">
          <path d="M2.5 1h2l1 2.8-1.3.9a6.5 6.5 0 0 0 3.1 3.1l.9-1.3L11 7.5v2a1.2 1.2 0 0 1-1.3 1.2A9.2 9.2 0 0 1 1.3 2.3 1.2 1.2 0 0 1 2.5 1z" fill="var(--bronze)"/>
        </svg>
        055-210 347 618
      </p>
      <p class="contact__line">
        <svg viewBox="0 0 12 12" aria-hidden="true">
          <circle cx="6" cy="6" r="5" fill="none" stroke="var(--bronze)" stroke-width="1.2"/>
          <ellipse cx="6" cy="6" rx="2.2" ry="5" fill="none" stroke="var(--bronze)" stroke-width="1"/>
          <line x1="1" y1="6" x2="11" y2="6" stroke="var(--bronze)" stroke-width="1"/>
        </svg>
        www.lashverastudio.example
      </p>
    </div>

    <div class="rule rule--upper"></div>

    <p class="address">4720 N.Alder Crest<br>Ave Beverly Hills , CA 90210</p>

    <div class="rule rule--lower"></div>

    <p class="follow">
      <span class="social-dot" aria-label="Circlebook"></span>
      <span class="social-dot" aria-label="Snapgrid"></span>
      <span class="follow__text">Follow us for seasonal campaign and news <span class="follow__handle">@lashverastudiolounge</span></span>
    </p>
  </section>

</main>
</body>
</html>
```